Home Remodeling company needs a business card design

we need a business card design for home remodeling company in hamilton county, indiana USA. we offers a wide range of construction services including whole house renovations, Design and Build Basements and Kitchen and Bathroom Remodeling . we would like to see designs for both site of business card that use the same color of the company logo and also including all information below :
1- Karim Feltous CEO / General Contractor
2- all company contacts Telephone numbers ( 1-888-DULOM-47 ) ( 317-555-0193) email address ( info@dulomhome.com) website ( www.dulomhome.com ) and social media logos (Facebook- twitter- google plus )
3- company logo
4- licensed . insured . bonded

```html
<!DOCTYPE html>
<html lang="en">
<head>
<meta charset="utf-8">
<title>Dulom Home Remodeling – Business Card</title>
<link href="https://fonts.googleapis.com/css2?family=Open+Sans:wght@400;600;700&display=swap" rel="stylesheet">
<style>
  :root {
    --brand-red: #c8323a;
    --ink-dark: #3b3b3d;
    --ink-mid: #6d6e71;
    --rule-grey: #b9b9bb;
    --panel-top: #5a5a5c;
    --panel-bottom: #2e2e30;
    --card-white: #ffffff;
    --stage: #e9e6e1;
  }
  * { box-sizing: border-box; margin: 0; padding: 0; }
  html, body {
    width: 1200px; height: 950px; overflow: hidden;
    background: var(--stage);
    font-family: "Open Sans", Arial, sans-serif;
  }
  .sheet {
    position: relative; width: 1200px; height: 950px;
    display: flex; flex-direction: column; align-items: center;
    justify-content: center; gap: 56px;
  }
  .card {
    position: relative; width: 680px; height: 388px;
    background: var(--card-white);
    box-shadow: 0 10px 30px rgba(0,0,0,.18);
    overflow: hidden;
  }

  /* Front side */
  .card-front {
    display: flex; flex-direction: column; align-items: center; justify-content: center;
  }
  .front-brand {
    display: flex; align-items: center; gap: 14px;
    margin-bottom: 44px;
  }
  .brand-square { width: 30px; height: 30px; background: var(--brand-red); }
  .front-brand .brand-name {
    font-size: 52px; font-weight: 700; letter-spacing: 4px; color: var(--ink-dark);
  }
  .credentials {
    font-size: 17px; letter-spacing: 1.5px; color: var(--brand-red);
    text-transform: uppercase;
  }
  .social-row {
    position: relative; width: 250px; height: 22px; margin-top: 8px;
    display: flex; align-items: center; justify-content: center; gap: 6px;
  }
  .social-row::before {
    content: ""; position: absolute; left: 0; right: 0; top: 50%;
    height: 1px; background: linear-gradient(90deg, transparent, var(--rule-grey) 25%, var(--rule-grey) 75%, transparent);
  }
  .social-dot {
    position: relative; width: 16px; height: 16px; border-radius: 50%;
    background: var(--ink-dark); box-shadow: 0 0 0 3px var(--card-white);
  }

  /* Back side */
  .back-top {
    position: absolute; left: 0; top: 0; width: 100%; height: 196px;
    display: flex; align-items: center; justify-content: center;
  }
  .back-brand { display: flex; align-items: center; gap: 14px; margin-top: 28px; }
  .back-brand .brand-square { width: 26px; height: 26px; }
  .back-brand .brand-name {
    font-size: 60px; font-weight: 700; letter-spacing: 5px; color: var(--ink-dark);
  }
  .back-rule {
    position: absolute; left: 0; top: 204px; width: 100%; height: 3px; background: var(--brand-red);
  }
  .back-panel {
    position: absolute; left: 0; top: 214px; width: 100%; bottom: 0;
    background: linear-gradient(160deg, var(--panel-top), var(--panel-bottom));
    display: flex; align-items: center;
  }
  .holder {
    width: 330px; padding-right: 34px; text-align: right; color: #fff;
  }
  .holder-name { font-size: 23px; font-weight: 700; }
  .holder-role { font-size: 17px; margin-top: 4px; color: #ececec; }
  .panel-divider { width: 1px; height: 110px; background: rgba(255,255,255,.45); }
  .contact-list {
    list-style: none; padding-left: 30px; color: #fff; font-size: 15px;
  }
  .contact-list li { display: flex; align-items: center; gap: 12px; line-height: 27px; }
  .contact-list svg { width: 15px; height: 15px; fill: #fff; flex: none; }
</style>
</head>
<body>
<main class="sheet">

  <section class="card card-front" aria-label="Card front">
    <div class="front-brand">
      <span class="brand-square"></span>
      <span class="brand-name">DULOM</span>
    </div>
    <p class="credentials">Licensed | Insured | Bonded</p>
    <div class="social-row" aria-label="Social media">
      <span class="social-dot"></span>
      <span class="social-dot"></span>
      <span class="social-dot"></span>
    </div>
  </section>

  <section class="card card-back" aria-label="Card back">
    <div class="back-top">
      <div class="back-brand">
        <span class="brand-square"></span>
        <span class="brand-name">DULOM</span>
      </div>
    </div>
    <div class="back-rule"></div>
    <div class="back-panel">
      <div class="holder">
        <p class="holder-name">Karim Feltous</p>
        <p class="holder-role">CEO / General Contractor</p>
      </div>
      <div class="panel-divider"></div>
      <ul class="contact-list">
        <li>
          <svg viewBox="0 0 16 16" aria-hidden="true"><path d="M3.6 1.2l2.3 2.9-1.3 1.8c.9 1.9 2.5 3.5 4.4 4.4l1.8-1.3 2.9 2.3-1.4 2.3C7.2 13.9 2.1 8.8 1.3 3.6z"/></svg>
          1-888-DULOM-47
        </li>
        <li>
          <svg viewBox="0 0 16 16" aria-hidden="true"><path d="M4.5 1h7a1 1 0 0 1 1 1v12a1 1 0 0 1-1 1h-7a1 1 0 0 1-1-1V2a1 1 0 0 1 1-1zm.6 2v9h5.8V3zM8 12.6a.8.8 0 1 0 0 1.6.8.8 0 0 0 0-1.6z"/></svg>
          317-555-0193
        </li>
        <li>
          <svg viewBox="0 0 16 16" aria-hidden="true"><path d="M1 3.5h14v9H1zm1.5 1.2v.3L8 8.6 13.5 5v-.3zm0 2v4.6h11V6.7L8 10.3z"/></svg>
          info@dulomhome.com
        </li>
        <li>
          <svg viewBox="0 0 16 16" aria-hidden="true"><path d="M8 1a7 7 0 1 0 0 14A7 7 0 0 0 8 1zm0 1.5c.8 0 1.7 1.6 2 4H6c.3-2.4 1.2-4 2-4zM2.6 7.5h2C4.6 6 4.9 4.6 5.4 3.6A5.5 5.5 0 0 0 2.6 7.5zm8.8 0h2a5.5 5.5 0 0 0-2.8-3.9c.5 1 .8 2.4.8 3.9zM6 8.5h4c-.2 2.6-1.1 5-2 5s-1.8-2.4-2-5zm-3.4 0a5.5 5.5 0 0 0 2.8 3.9c-.5-1-.8-2.4-.8-3.9zm8.8 0c0 1.5-.3 2.9-.8 3.9a5.5 5.5 0 0 0 2.8-3.9z"/></svg>
          www.dulomhome.com
        </li>
      </ul>
    </div>
  </section>

</main>
</body>
</html>
```